Business Card for Coastal Tundrabridge Advisory

We need a business card for Coastal Tundrabridge Advisory. The company website address is provided below. The company logo is attached. We provide specialized permafrost services to the mining, transportation, and oil & gas industries. The card should be prepared for:
Matthias Korhonen, PhD.
Coastal Tundrabridge Advisory
PO Box 418259
Quillwater, Alaska 99642
Direct: +1-907-555-0143
Email: mkorhonen@tundrabridgeadvisory.example
Website: www.coastaltundrabridgeadvisory.example

```html
<!DOCTYPE html>
<html lang="en">
<head>
<meta charset="utf-8">
<title>Coastal Tundrabridge Advisory — Business Card</title>
<link rel="stylesheet" href="https://fonts.googleapis.com/css2?family=Poppins:wght@400;700&display=swap">
<style>
  :root {
    --page-bg: #e9e6e1;
    --card-white: #ffffff;
    --ink: #14181c;
    --ink-soft: #3a3f44;
    --tundra-green: #6f8a45;
    --tundra-olive: #7a7b52;
    --tundra-deep: #5f7a3a;
    --logo-light: #ffffff;
  }
  * { box-sizing: border-box; margin: 0; padding: 0; }
  html, body {
    width: 1200px; height: 900px; overflow: hidden;
    background: var(--page-bg);
    font-family: "Poppins", sans-serif;
    color: var(--ink);
  }
  .sheet {
    position: relative; width: 1200px; height: 900px;
    display: flex; flex-direction: column; align-items: center;
    justify-content: center; gap: 34px;
  }
  .card {
    position: relative; width: 700px; height: 400px; overflow: hidden;
    box-shadow: 0 6px 18px rgba(0,0,0,.18);
  }
  /* Front */
  .card-front { border-radius: 44px 0 44px 0; }
  .aerial-photo {
    position: absolute; inset: 0;
    background: linear-gradient(160deg, var(--tundra-olive) 0%, var(--tundra-green) 55%, var(--tundra-deep) 100%);
  }
  .front-wordmark {
    position: absolute; right: 60px; bottom: 72px; text-align: right;
    color: var(--logo-light); font-weight: 700; text-transform: uppercase;
    font-size: 30px; line-height: 1.2; letter-spacing: 3px;
  }
  /* Back */
  .card-back { background: var(--card-white); border-radius: 0 48px 0 48px; }
  .holder { position: absolute; left: 44px; top: 40px; }
  .holder-name { font-weight: 700; font-size: 26px; line-height: 1.2; }
  .holder-company { font-weight: 400; font-size: 16px; color: var(--ink-soft); }
  .contact-list {
    position: absolute; left: 44px; top: 148px; list-style: none;
    font-size: 15px; color: var(--ink-soft); line-height: 1.75;
  }
  .contact-list li { display: flex; align-items: center; gap: 10px; }
  .contact-list svg { width: 15px; height: 15px; fill: var(--ink); flex: none; }
  .tagline {
    position: absolute; left: 44px; bottom: 38px; width: 230px;
    font-size: 14px; line-height: 1.4; color: var(--ink-soft);
  }
  .back-wordmark {
    position: absolute; right: 44px; bottom: 52px; text-align: right;
    color: var(--ink); font-weight: 700; text-transform: uppercase;
    font-size: 22px; line-height: 1.2; letter-spacing: 2px;
  }
</style>
</head>
<body>
<main class="sheet">
  <section class="card card-front">
    <div class="aerial-photo" role="img" aria-label="Aerial photograph of Alaskan tundra with thaw lakes and meltwater channels"></div>
    <p class="front-wordmark">Coastal<br>Tundrabridge Advisory</p>
  </section>

  <section class="card card-back">
    <div class="holder">
      <h1 class="holder-name">Matthias Korhonen, PhD.</h1>
      <p class="holder-company">Coastal Tundrabridge Advisory</p>
    </div>
    <ul class="contact-list">
      <li><svg viewBox="0 0 24 24" aria-hidden="true"><path d="M6.6 10.8a15.1 15.1 0 0 0 6.6 6.6l2.2-2.2a1 1 0 0 1 1-.25 11.4 11.4 0 0 0 3.6.57 1 1 0 0 1 1 1V20a1 1 0 0 1-1 1A17 17 0 0 1 3 4a1 1 0 0 1 1-1h3.5a1 1 0 0 1 1 1c0 1.25.2 2.45.57 3.57a1 1 0 0 1-.25 1z"/></svg>+1-907-555-0143</li>
      <li><svg viewBox="0 0 24 24" aria-hidden="true"><path d="M2 5h20v14H2z M2 5l10 8 10-8" fill="none" stroke="#14181c" stroke-width="2"/></svg>mkorhonen@tundrabridgeadvisory.example</li>
      <li><svg viewBox="0 0 24 24" aria-hidden="true"><g fill="none" stroke="#14181c" stroke-width="2"><circle cx="12" cy="12" r="9"/><ellipse cx="12" cy="12" rx="4" ry="9"/><path d="M3 12h18"/></g></svg>www.coastaltundrabridgeadvisory.example</li>
      <li><svg viewBox="0 0 24 24" aria-hidden="true"><path d="M12 2a7 7 0 0 0-7 7c0 5.2 7 13 7 13s7-7.8 7-13a7 7 0 0 0-7-7zm0 9.5A2.5 2.5 0 1 1 12 6.5a2.5 2.5 0 0 1 0 5z"/></svg>PO Box 418259, Quillwater, Alaska 99642</li>
    </ul>
    <p class="tagline">We Provide Specialized Permafrost Services To The Mining, Transportation, And Oil &amp; Gas Industries</p>
    <p class="back-wordmark">Coastal<br>Tundrabridge Advisory</p>
  </section>
</main>
</body>
</html>
```